Redesign of business card for Cedar Ridge Mechanical

We are looking for a new design for our business cards for Cedar Ridge Mechanical. We are a plumbing & HVAC construction company, operating on the West Coast of Canada and USA. Logo attached.
Industry/Entity Type
Construction - Plumbing & HVAC
Contact Information for Business Card
Name, address, phone numbers, email, website address
Look and feel
Each slider illustrates characteristics of the customer's brand and the style your logo design should communicate.

```html
<!DOCTYPE html>
<html lang="en">
<head>
<meta charset="utf-8">
<title>Cedar Ridge Mechanical – Business Cards</title>
<link href="https://fonts.googleapis.com/css2?family=Montserrat:wght@400;500;700&display=swap" rel="stylesheet">
<style>
  :root {
    --backdrop: #232323;
    --card: #ffffff;
    --ink: #111111;
    --ink-soft: #3a3a3a;
    --rule: #2a2a2a;
  }
  * { box-sizing: border-box; margin: 0; padding: 0; }
  html, body {
    width: 1200px;
    height: 780px;
    overflow: hidden;
    background: var(--backdrop);
    font-family: "Montserrat", sans-serif;
    color: var(--ink);
  }
  .canvas {
    position: relative;
    width: 1200px;
    height: 780px;
    display: flex;
    align-items: center;
    justify-content: center;
    gap: 40px;
  }
  .card {
    position: relative;
    width: 540px;
    height: 309px;
    background: var(--card);
    box-shadow: 0 18px 40px rgba(0, 0, 0, 0.55);
  }

  /* Contact side */
  .card--contact .brand {
    position: absolute;
    left: 34px;
    top: 64px;
    width: 200px;
    display: flex;
    align-items: center;
    gap: 10px;
  }
  .brand__mark {
    flex: 0 0 auto;
    width: 14px;
    height: 14px;
    background: var(--ink);
  }
  .brand__name {
    font-weight: 700;
    font-size: 17px;
    line-height: 1.2;
    letter-spacing: 0.04em;
    text-transform: uppercase;
    color: var(--ink);
  }
  .divider {
    position: absolute;
    left: 254px;
    top: 40px;
    width: 1px;
    height: 150px;
    background: var(--rule);
  }
  .person {
    position: absolute;
    left: 278px;
    top: 48px;
  }
  .person__name {
    font-weight: 700;
    font-size: 22px;
    letter-spacing: 0.03em;
    text-transform: uppercase;
  }
  .person__title {
    margin-top: 4px;
    font-weight: 400;
    font-size: 14px;
    color: var(--ink-soft);
  }
  .contacts {
    list-style: none;
    margin-top: 18px;
    display: grid;
    gap: 8px;
  }
  .contacts li {
    display: flex;
    align-items: center;
    gap: 9px;
    font-size: 14px;
    font-weight: 400;
  }
  .contacts svg { width: 12px; height: 12px; fill: var(--ink); flex: 0 0 auto; }
  .address {
    position: absolute;
    left: 34px;
    bottom: 34px;
    font-size: 14px;
    font-weight: 400;
  }

  /* Logo side */
  .card--front {
    display: flex;
    align-items: center;
    justify-content: center;
  }
  .card--front .brand {
    display: flex;
    align-items: center;
    gap: 16px;
  }
  .card--front .brand__mark { width: 24px; height: 24px; }
  .card--front .brand__name { font-size: 28px; }
</style>
</head>
<body>
<main class="canvas">

  <section class="card card--contact" aria-label="Business card, contact side">
    <div class="brand">
      <span class="brand__mark" aria-hidden="true"></span>
      <span class="brand__name">Cedar Ridge Mechanical</span>
    </div>
    <span class="divider" aria-hidden="true"></span>
    <div class="person">
      <h1 class="person__name">Daniel Harper</h1>
      <p class="person__title">Managing Director</p>
      <ul class="contacts">
        <li>
          <svg viewBox="0 0 24 24" aria-hidden="true"><path d="M6.6 10.8a15.1 15.1 0 0 0 6.6 6.6l2.2-2.2a1 1 0 0 1 1-.25 11.4 11.4 0 0 0 3.6.57 1 1 0 0 1 1 1V20a1 1 0 0 1-1 1A17 17 0 0 1 3 4a1 1 0 0 1 1-1h3.5a1 1 0 0 1 1 1c0 1.25.2 2.45.57 3.57a1 1 0 0 1-.25 1z"/></svg>
          123 456 789
        </li>
        <li>
          <svg viewBox="0 0 24 24" aria-hidden="true"><path d="M2 5h20v14H2z M4 7v.5l8 5 8-5V7l-8 5z" fill-rule="evenodd"/></svg>
          info@yourgmail.com
        </li>
        <li>
          <svg viewBox="0 0 24 24" aria-hidden="true"><circle cx="12" cy="12" r="10"/></svg>
          www.yourwebsite.com
        </li>
      </ul>
    </div>
    <p class="address">Your address, City State, Zip 1234</p>
  </section>

  <section class="card card--front" aria-label="Business card, logo side">
    <div class="brand">
      <span class="brand__mark" aria-hidden="true"></span>
      <span class="brand__name">Cedar Ridge Mechanical</span>
    </div>
  </section>

</main>
</body>
</html>
```